Business card design for my company.
I would like the card's background colour to be black. You can also see our web site to get an idea of our brand. https://www.tmwhomecrafting.com.au/
- Name
- Email

```html
<!DOCTYPE html>
<html lang="en">
<head>
<meta charset="utf-8">
<title>TMW Home Crafting – Business Card</title>
<link rel="stylesheet" href="https://fonts.googleapis.com/css2?family=Montserrat:wght@400;500;700&display=swap">
<style>
  :root {
    --page-bg: #2b2b2d;
    --card-bg: #1f1f21;
    --card-bg-light: #262628;
    --brand-green: #12913f;
    --text-white: #f2f2f2;
    --text-muted: #d8d8d8;
  }
  * { box-sizing: border-box; margin: 0; padding: 0; }
  html, body {
    width: 1200px;
    height: 836px;
    overflow: hidden;
    background: var(--page-bg);
    font-family: "Montserrat", sans-serif;
  }
  .stage {
    width: 1200px;
    height: 836px;
    display: flex;
    flex-direction: column;
    align-items: center;
    justify-content: center;
    gap: 40px;
  }
  .card {
    position: relative;
    width: 600px;
    height: 343px;
    background: var(--card-bg);
    border-left: 3px solid var(--brand-green);
    border-bottom: 3px solid var(--brand-green);
    box-shadow: 0 14px 30px rgba(0,0,0,0.45);
    overflow: hidden;
  }

  /* Front */
  .card-front { display: flex; align-items: center; }
  .front-brand {
    width: 300px;
    height: 100%;
    display: flex;
    align-items: center;
    justify-content: center;
    gap: 10px;
  }
  .brand-mark {
    width: 14px;
    height: 14px;
    background: var(--brand-green);
  }
  .brand-name {
    color: var(--text-white);
    font-weight: 700;
    font-size: 20px;
    letter-spacing: 2px;
    text-transform: uppercase;
  }
  .front-divider {
    width: 2px;
    height: 190px;
    background: var(--brand-green);
  }
  .front-details { padding-left: 30px; }
  .person-name {
    color: var(--brand-green);
    font-weight: 700;
    font-size: 28px;
    line-height: 1.1;
  }
  .person-title {
    color: var(--text-white);
    font-size: 14px;
    margin-top: 4px;
    margin-bottom: 18px;
  }
  .contact-list { list-style: none; }
  .contact-item {
    display: flex;
    align-items: center;
    gap: 10px;
    color: var(--text-muted);
    font-size: 12px;
    margin-bottom: 9px;
  }
  .contact-icon { width: 18px; height: 18px; flex: none; }

  /* Back */
  .card-back {
    display: flex;
    align-items: center;
    justify-content: center;
  }
  .back-texture {
    position: absolute;
    inset: 0;
    background: linear-gradient(135deg, var(--card-bg-light), var(--card-bg));
  }
  .back-brand {
    position: relative;
    display: flex;
    align-items: center;
    gap: 14px;
  }
  .back-brand .brand-mark { width: 20px; height: 20px; }
  .back-brand .brand-name { font-size: 32px; letter-spacing: 3px; }
</style>
</head>
<body>
<main class="stage">

  <section class="card card-front">
    <div class="front-brand">
      <span class="brand-mark"></span>
      <span class="brand-name">TMW Home Crafting</span>
    </div>
    <div class="front-divider"></div>
    <div class="front-details">
      <h1 class="person-name">Liam Hartley</h1>
      <p class="person-title">General Manager</p>
      <ul class="contact-list">
        <li class="contact-item">
          <svg class="contact-icon" viewBox="0 0 18 18"><circle cx="9" cy="9" r="9" fill="#12913f"/><path d="M9 4a3 3 0 0 0-3 3c0 2.3 3 6 3 6s3-3.7 3-6a3 3 0 0 0-3-3z" fill="#fff"/><circle cx="9" cy="7" r="1.1" fill="#12913f"/></svg>
          Eastvale, Tasmania, Australia
        </li>
        <li class="contact-item">
          <svg class="contact-icon" viewBox="0 0 18 18"><circle cx="9" cy="9" r="9" fill="#12913f"/><path d="M6 4.5l2 2-1 1.2c.6 1.3 1.5 2.2 2.8 2.8l1.2-1 2 2-1.2 1.5C8.5 12.5 5.5 9.5 4.5 5.7z" fill="#fff"/></svg>
          0400 123 456
        </li>
        <li class="contact-item">
          <svg class="contact-icon" viewBox="0 0 18 18"><circle cx="9" cy="9" r="9" fill="#12913f"/><rect x="4.5" y="5.8" width="9" height="6.4" fill="#fff"/><path d="M4.5 5.8L9 9.5l4.5-3.7" fill="none" stroke="#12913f" stroke-width="1"/></svg>
          info@tmwhomecrafting.com.au
        </li>
        <li class="contact-item">
          <svg class="contact-icon" viewBox="0 0 18 18"><circle cx="9" cy="9" r="9" fill="#12913f"/><circle cx="9" cy="9" r="4.5" fill="none" stroke="#fff" stroke-width="1.2"/><path d="M4.5 9h9M9 4.5c-2 2.5-2 6.5 0 9M9 4.5c2 2.5 2 6.5 0 9" fill="none" stroke="#fff" stroke-width="1"/></svg>
          www.tmwhomecrafting.com.au
        </li>
      </ul>
    </div>
  </section>

  <section class="card card-back">
    <div class="back-texture" role="img" aria-label="Subtle embossed chevron texture across the dark card face"></div>
    <div class="back-brand">
      <span class="brand-mark"></span>
      <span class="brand-name">TMW Home Crafting</span>
    </div>
  </section>

</main>
</body>
</html>
```